GlassHaven Artbook for Okanagan Region, British Columbia

Creating an art book: GlassHaven, for the Okanagan Wine Region in British Columbia, Canada. Would like smart, modern, clean and linear...cool, sexy urban, not ugly boring suburban... I need a cover that appeals to the wino in all of us! Title: GlassHaven -Marla Dovicki
Updates
Thank you all kindly for your efforts. I have added some files so that you can get a sense of my aesthetic...it's never easy trying to figure it out, is it? I will hopefully have dimensions of book soon...cheers, Marla
would anyone please design a giant wine bottle with the wine label that looks like a label but says glasshaven...just curious to see if it works as a design or not...thank you.
Target Market(s)
Designing this wine art book of quotes to wineries in Okanagan BC. Buyer is wine lover and tourist ready to spend his vacation bucks on this wonderful book!
Look and feel

```html
<!DOCTYPE html>
<html lang="en">
<head>
<meta charset="UTF-8">
<title>GlassHaven — Book Cover</title>
<link rel="stylesheet" href="https://fonts.googleapis.com/css2?family=Poppins:ital,wght@0,300;1,300&display=swap">
<style>
  :root {
    --page-bg: #ffffff;
    --cover-top: #e4e4e4;
    --cover-bottom: #d3d3d3;
    --title-ink: #2a2526;
    --soft-text: #3a3a3a;
    --bottle-yellow: rgba(224, 214, 120, 0.55);
    --bottle-red: rgba(196, 70, 82, 0.55);
    --bottle-rose: rgba(226, 140, 140, 0.55);
    --bottle-green: rgba(110, 180, 130, 0.55);
    --bottle-orange: rgba(214, 130, 80, 0.55);
  }
  * { margin: 0; padding: 0; box-sizing: border-box; }
  html, body {
    width: 1200px;
    height: 1200px;
    overflow: hidden;
    background: var(--page-bg);
  }
  .canvas {
    position: relative;
    width: 1200px;
    height: 1200px;
    background: var(--page-bg);
  }
  .book-cover {
    position: absolute;
    left: 290px;
    top: 50px;
    width: 620px;
    height: 1100px;
    background: linear-gradient(180deg, var(--cover-top) 0%, var(--cover-bottom) 100%);
    overflow: hidden;
  }
  .bottle-artwork {
    position: absolute;
    left: 40px;
    top: 60px;
    width: 410px;
    height: 960px;
    border-radius: 120px 120px 60px 60px;
    background:
      radial-gradient(ellipse at 30% 12%, var(--bottle-yellow) 0%, transparent 45%),
      radial-gradient(ellipse at 75% 25%, var(--bottle-rose) 0%, transparent 50%),
      radial-gradient(ellipse at 40% 55%, var(--bottle-orange) 0%, transparent 55%),
      radial-gradient(ellipse at 55% 85%, var(--bottle-green) 0%, transparent 50%),
      linear-gradient(180deg, rgba(214, 150, 130, 0.35) 0%, var(--bottle-red) 70%, rgba(150, 190, 160, 0.45) 100%);
    opacity: 0.85;
  }
  .author-name {
    position: absolute;
    right: 40px;
    top: 118px;
    font-family: "Poppins", sans-serif;
    font-style: italic;
    font-weight: 300;
    font-size: 20px;
    letter-spacing: 2.5px;
    color: var(--soft-text);
  }
  .book-title {
    position: absolute;
    right: 40px;
    top: 610px;
    font-family: "Poppins", sans-serif;
    font-style: normal;
    font-weight: 300;
    font-size: 72px;
    line-height: 1;
    letter-spacing: 1px;
    color: var(--title-ink);
    white-space: nowrap;
  }
  .region-label {
    position: absolute;
    right: 40px;
    top: 880px;
    text-align: right;
    font-family: "Poppins", sans-serif;
    font-style: italic;
    font-weight: 300;
    font-size: 19px;
    line-height: 29px;
    letter-spacing: 2px;
    color: var(--soft-text);
  }
</style>
</head>
<body>
  <div class="canvas">
    <section class="book-cover">
      <div class="bottle-artwork" role="img" aria-label="Overlapping translucent wine bottle silhouettes in yellow, red, rose, orange and green"></div>
      <p class="author-name">Marla Dovicki</p>
      <h1 class="book-title">GlassHaven</h1>
      <p class="region-label">Okanagan<br>Wine<br>Region</p>
    </section>
  </div>
</body>
</html>
```